Talvique Hotels Business Card and Logo

We need a business card design for a hotel group. I saw a hotel card you designed and really liked it. We have multiple properties with different brands. Were hoping that the card would be unique and find a way to list out all our properties. Our web address is www.talviquehotels.com. I have attached some photos of card designs I like.

Industry/Entity Type

Hotel

Contact Information for Business Card

Scott CurranReneson HotelsChief Operating Officer56 Madera DriveCorte Madera, CA 94925Office 415-891-5013Cell 707-5550143

```html
<!DOCTYPE html>
<html lang="en">
<head>
<meta charset="utf-8">
<title>Talvique Hotels Business Card</title>
<link rel="stylesheet" href="https://fonts.googleapis.com/css2?family=Lato:wght@400;700;900&display=swap">
<style>
  :root {
    --stage: #3b3c40;
    --orange: #f26a21;
    --navy: #27307a;
    --ink: #1d1d1f;
    --grey: #7a7a7a;
    --card-white: #ffffff;
    --card-black: #0b0b0b;
  }
  * { box-sizing: border-box; margin: 0; padding: 0; }
  html, body {
    width: 1200px; height: 900px; overflow: hidden;
    background: var(--stage);
    font-family: "Lato", sans-serif;
  }
  .stage {
    width: 1200px; height: 900px;
    display: flex; flex-direction: column; align-items: center; justify-content: center;
    gap: 40px;
  }
  .card {
    width: 660px; height: 377px;
    border-radius: 30px;
    position: relative;
    overflow: hidden;
  }
  .card--back { background: var(--card-black); display: flex; align-items: center; justify-content: center; }
  .card--front { background: var(--card-white); display: flex; align-items: center; }

  .brand { display: flex; align-items: center; gap: 14px; }
  .brand__square { width: 22px; height: 22px; background: var(--orange); flex: none; }
  .brand__name { font-weight: 900; font-size: 34px; letter-spacing: 0.5px; white-space: nowrap; }
  .card--back .brand__name { color: var(--orange); }
  .card--front .brand__name { color: var(--navy); font-size: 30px; }

  .front__logo { width: 340px; display: flex; justify-content: center; }
  .front__rule { width: 2px; height: 190px; background: var(--orange); flex: none; }
  .front__details { padding-left: 30px; }

  .person__name { font-weight: 900; font-size: 30px; line-height: 1.05; white-space: nowrap; }
  .person__first { color: var(--orange); }
  .person__last { color: var(--navy); }
  .person__title { color: var(--grey); font-size: 15px; margin-top: 4px; letter-spacing: 0.3px; }

  .address { color: var(--ink); font-size: 15px; line-height: 1.4; margin-top: 20px; }

  .contact { list-style: none; margin-top: 10px; }
  .contact__item {
    display: flex; align-items: center; gap: 10px;
    color: var(--ink); font-size: 15px; line-height: 1; margin-top: 10px;
  }
  .contact__icon { width: 18px; height: 18px; flex: none; }
</style>
</head>
<body>
  <main class="stage">
    <section class="card card--back" aria-label="Card back">
      <div class="brand">
        <span class="brand__square"></span>
        <span class="brand__name">Talvique Hotels</span>
      </div>
    </section>

    <section class="card card--front" aria-label="Card front">
      <div class="front__logo">
        <div class="brand">
          <span class="brand__square"></span>
          <span class="brand__name">Talvique Hotels</span>
        </div>
      </div>
      <div class="front__rule"></div>
      <div class="front__details">
        <h1 class="person__name"><span class="person__first">Brent</span> <span class="person__last">Holloway</span></h1>
        <p class="person__title">Chief Operating Officer</p>
        <p class="address">83 Pellwick Lane Larkmoor,<br>CA 96071</p>
        <ul class="contact">
          <li class="contact__item">
            <svg class="contact__icon" viewBox="0 0 18 18" aria-hidden="true">
              <rect x="5" y="1.5" width="8" height="15" rx="1.5" fill="none" stroke="var(--orange)" stroke-width="1.5"/>
              <line x1="8" y1="14" x2="10" y2="14" stroke="var(--orange)" stroke-width="1.5"/>
            </svg>
            707-5550143
          </li>
          <li class="contact__item">
            <svg class="contact__icon" viewBox="0 0 18 18" aria-hidden="true">
              <path d="M2 6 Q9 1 16 6 L14 8 L11.5 6.5 L6.5 6.5 L4 8 Z" fill="var(--orange)"/>
              <rect x="3" y="9" width="12" height="7" rx="1.5" fill="var(--orange)"/>
              <circle cx="9" cy="12.5" r="2" fill="var(--card-white)"/>
            </svg>
            415-555-0186
          </li>
          <li class="contact__item">
            <svg class="contact__icon" viewBox="0 0 18 18" aria-hidden="true">
              <circle cx="9" cy="9" r="7.5" fill="var(--orange)"/>
              <g fill="none" stroke="var(--card-white)" stroke-width="1">
                <ellipse cx="9" cy="9" rx="3" ry="7.5"/>
                <line x1="1.5" y1="9" x2="16.5" y2="9"/>
                <line x1="9" y1="1.5" x2="9" y2="16.5"/>
              </g>
            </svg>
            www.talviquehotels.com
          </li>
        </ul>
      </div>
    </section>
  </main>
</body>
</html>
```